Best local air conditioning and heating contractor

We need a website design for a new company in Tampa Bay called the Coastal Breeze Cooling Company. We provide superior services for residential and commercial properties as well as maintenance and installing HVAC systems. We also want to sell equipment, parts and filter on the website as well. We want it easy to use for customers. Rich with content and keywords for our area.

Target Market(s)

homeowners in Tampa Bay

Industry/Entity Type

HVAC air conditioning and heating

Coding

Coded - Design and coding required

Number of Pages Required

5+ page

Font styles to use
Sans Serif

Requirements
Nice to have
• would like the colors to be same as logo

```html
<!DOCTYPE html>
<html lang="en">
<head>
<meta charset="utf-8">
<title>Coastal Breeze Cooling Company</title>
<link href="https://fonts.googleapis.com/css2?family=Michroma&family=Roboto:wght@400;500;700&display=swap" rel="stylesheet">
<style>
:root{
  --red:#d71e25;
  --red-dark:#b3151b;
  --navy:#1f3170;
  --navy-dark:#182659;
  --ink:#222;
  --muted:#444;
  --light:#eef0f4;
  --white:#fff;
}
*{margin:0;padding:0;box-sizing:border-box}
html,body{width:1200px;height:4528px;overflow:hidden}
body{position:relative;background:var(--white);font-family:'Roboto',Arial,sans-serif;color:var(--ink)}
.abs{position:absolute}
.display{font-family:'Michroma','Arial',sans-serif;font-weight:400;letter-spacing:0}
.red{color:var(--red)}
.navy{color:var(--navy)}
.btn{position:absolute;background:var(--red);color:#fff;font-weight:700;font-size:14px;display:flex;align-items:center;justify-content:center;letter-spacing:.3px}
.ph{position:absolute}
/* header */
.topline{top:0;left:0;width:1200px;height:5px;background:var(--red)}
.brand{left:112px;top:55px;display:flex;align-items:center;gap:12px;font-weight:700;font-size:19px;color:var(--navy);width:260px;line-height:1.2}
.brand .dot{width:34px;height:34px;border-radius:50%;background:var(--red);flex:none}
.contact-chip{display:flex;align-items:center;gap:12px}
.chip-icon{width:38px;height:38px;border-radius:50%;background:var(--red);display:flex;align-items:center;justify-content:center}
.chip-label{font-size:10px;font-weight:700;color:var(--navy)}
.chip-value{font-size:17px;color:var(--ink);margin-top:2px}
.nav{top:110px;left:476px;display:flex;gap:34px;font-size:16px;font-weight:500;color:var(--ink)}
.nav .active{color:var(--red)}
/* hero */
.hero-title{top:340px;left:0;width:895px;text-align:center;font-size:44px;color:var(--navy)}
.hero-sub{top:390px;left:0;width:895px;text-align:center;font-size:36px;color:var(--red)}
.hero-text{top:455px;left:170px;width:555px;text-align:center;font-size:18px;line-height:28px;color:#222}
.arrow{position:absolute;width:34px;height:34px;background:#fff;transform:rotate(45deg)}
/* about */
.about-title{top:945px;left:112px;font-size:38px;color:var(--navy)}
.about-sub{top:1012px;left:112px;font-size:22px;line-height:32px;color:var(--ink)}
.about-p{font-size:14px;line-height:26.5px;color:var(--muted)}
/* sections */
.section-title{left:0;width:1200px;text-align:center;font-size:42px}
.svc-card{position:absolute;top:1957px;width:267px;height:360px}
.svc-card .cap{position:absolute;left:0;bottom:30px;width:100%;text-align:center;color:#fff;font-weight:700;font-size:16px;line-height:26px}
.prod-card{position:absolute;top:2577px;width:304px;height:333px;background:#fff;text-align:center}
.prod-card .name{position:absolute;top:218px;width:100%;color:var(--navy);font-weight:700;font-size:16px;line-height:27px}
.prod-card .go{position:absolute;left:136px;top:283px;width:30px;height:30px;background:var(--red);transform:rotate(45deg)}
.testi{position:absolute;top:3200px;width:305px;height:260px;background:#fff;box-shadow:0 4px 14px rgba(31,49,112,.14);padding:22px 24px}
.stars{color:#f4a622;font-size:14px;letter-spacing:2px}
.testi p{margin-top:10px;font-size:13.5px;line-height:23px;color:var(--muted);text-align:justify}
.testi hr{border:0;border-top:1px solid #ddd;margin:16px 0 14px}
.who{display:flex;align-items:center;gap:12px}
.avatar{width:54px;height:54px;border-radius:50%;flex:none}
.who b{display:block;color:var(--navy);font-size:16px;font-weight:700}
.who span{font-size:12px;color:var(--ink)}
.field{position:absolute;background:#fff;font-size:13px;color:#333;padding:12px 16px}
.foot-h{position:absolute;top:4240px;color:#fff;font-weight:700;font-size:19px}
.foot-list{position:absolute;top:4290px;color:#fff;font-size:14px;line-height:33px}
.social{position:absolute;top:4460px;width:36px;height:36px;border-radius:50%;background:#fff}
</style>
</head>
<body>

<!-- header -->
<div class="abs topline"></div>
<div class="abs brand"><span class="dot"></span><span>COASTAL BREEZE COOLING COMPANY</span></div>

<div class="abs contact-chip" style="left:604px;top:44px">
  <div class="chip-icon"><svg width="18" height="18" viewBox="0 0 24 24"><path fill="#fff" d="M6.6 10.8a15 15 0 0 0 6.6 6.6l2.2-2.2c.3-.3.7-.4 1-.2 1.1.4 2.3.6 3.6.6.6 0 1 .4 1 1V20c0 .6-.4 1-1 1A17 17 0 0 1 3 4c0-.6.4-1 1-1h3.5c.6 0 1 .4 1 1 0 1.2.2 2.4.6 3.6.1.3 0 .7-.2 1z"/></svg></div>
  <div><div class="chip-label">CALL US:</div><div class="chip-value">+1 (888) 888 8888</div></div>
</div>
<div class="abs contact-chip" style="left:828px;top:44px">
  <div class="chip-icon"><svg width="18" height="18" viewBox="0 0 24 24"><path fill="#fff" d="M3 5h18v14H3z"/><path fill="none" stroke="#d71e25" stroke-width="2" d="M3 6l9 7 9-7"/></svg></div>
  <div><div class="chip-label">EMAIL US:</div><div class="chip-value">info@coastalbreezecooling.com</div></div>
</div>

<nav class="abs nav">
  <span class="active">HOME</span><span>ABOUT US</span><span>OUR SERVICES</span><span>OUR PRODUCTS</span><span>CONTACT US</span>
</nav>

<!-- hero -->
<svg class="abs" style="left:0;top:162px" width="1200" height="710" viewBox="0 0 1200 710">
  <defs>
    <linearGradient id="heroFill" x1="0" x2="1" y1="0" y2="0">
      <stop offset="0" stop-color="#ffffff"/>
      <stop offset=".35" stop-color="#eef0f3"/>
      <stop offset=".7" stop-color="#b8c2cf"/>
      <stop offset="1" stop-color="#8fa3ba"/>
    </linearGradient>
  </defs>
  <g role="img" aria-label="Two HVAC technicians in safety gear inspecting rooftop air conditioning units">
    <polygon points="0,0 1200,0 1200,478 598,640 0,478" fill="url(#heroFill)"/>
  </g>
  <polygon points="0,478 598,640 1200,478 1200,486 598,700 0,486" fill="#d71e25"/>
</svg>
<div class="arrow" style="left:-17px;top:385px"></div>
<svg class="abs" style="left:4px;top:395px" width="12" height="14"><path d="M9 1 3 7l6 6" fill="none" stroke="#d71e25" stroke-width="2"/></svg>
<div class="arrow" style="left:1183px;top:385px"></div>
<svg class="abs" style="left:1184px;top:395px" width="12" height="14"><path d="M3 1l6 6-6 6" fill="none" stroke="#d71e25" stroke-width="2"/></svg>

<h1 class="abs display hero-title">COASTAL BREEZE</h1>
<div class="abs display hero-sub">COOLING COMPANY</div>
<p class="abs hero-text">Lorem ipsum dolor sit amet, consectetur adipiscing elit, sed do eiusmod tempor incididunt ut laborea.</p>
<div class="btn" style="left:381px;top:531px;width:110px;height:45px">CONTACT US</div>

<!-- about -->
<h2 class="abs display about-title">ABOUT <span class="red">US</span></h2>
<div class="abs display about-sub">COASTAL BREEZE<br>COOLING COMPANY</div>
<p class="abs about-p" style="left:112px;top:1086px;width:474px;text-align:justify">Lorem ipsum dolor sit amet, consectetur adipiscing elit, sed do eiusmod tempor incididunt ut labore et dolore magna aliqua. Ut enim ad minim veniam, quis nostrud exercitation ullamco laboris nisi ut aliquip ex ea commodo consequat duis aute irure dolor.</p>
<p class="abs about-p" style="left:614px;top:920px;width:474px;text-align:justify">Lorem ipsum dolor sit amet, consectetur adipiscing elit, sed do eiusmod tempor incididunt ut labore et dolore magna aliqua. Ut enim ad minim veniam, quis nostrud exercitation ullamco laboris nisi ut aliquip ex ea commodo consequat duis aute irure dolor in reprehendea in voluptate velit esse cillum dolore eu fugiat nulla pariatur. Excepteur sint occaecat cupidatat non proidentea.</p>
<p class="abs about-p" style="left:614px;top:1092px;width:474px;text-align:justify">Lorem ipsum dolor sit amet, consectetur adipiscing elit, sed do eiusmod tempor incididunt ut labore et dolore magna aliqua. Ut enim ad minim veniam, quis nostrud exercitation ullamcoea.</p>
<div class="btn" style="left:614px;top:1203px;width:132px;height:47px">LEARN MORE</div>
<div class="abs contact-chip" style="left:762px;top:1206px">
  <div class="chip-icon" style="background:#fff;box-shadow:0 2px 8px rgba(0,0,0,.15)"><svg width="16" height="16" viewBox="0 0 24 24"><path fill="#d71e25" d="M6.6 10.8a15 15 0 0 0 6.6 6.6l2.2-2.2c.3-.3.7-.4 1-.2 1.1.4 2.3.6 3.6.6.6 0 1 .4 1 1V20c0 .6-.4 1-1 1A17 17 0 0 1 3 4c0-.6.4-1 1-1h3.5c.6 0 1 .4 1 1 0 1.2.2 2.4.6 3.6.1.3 0 .7-.2 1z"/></svg></div>
  <div><div class="chip-label">CALL US:</div><div class="chip-value">+1 (888) 888 8888</div></div>
</div>

<div class="ph" role="img" aria-label="Technician with toolbox next to a wall-mounted air conditioner" style="left:180px;top:1230px;width:340px;height:338px;background:linear-gradient(135deg,#e8ecf1,#b8c4d2)"></div>
<svg class="abs" style="left:366px;top:1580px" width="118" height="52" aria-hidden="true">
  <defs><pattern id="dots" width="8" height="8" patternUnits="userSpaceOnUse"><circle cx="2" cy="2" r="1.3" fill="#777"/></pattern></defs>
  <rect width="118" height="52" fill="url(#dots)"/>
</svg>
<div class="abs" style="left:497px;top:1313px;width:523px;height:339px;background:#fff"></div>
<div class="ph" role="img" aria-label="Two technicians reviewing rooftop condenser units" style="left:533px;top:1313px;width:487px;height:339px;background:linear-gradient(135deg,#cdd5df,#8a9bb0)"></div>

<!-- services -->
<div class="abs" style="left:0;top:1767px;width:1200px;height:638px;background:var(--light)"></div>
<h2 class="abs display section-title navy" style="top:1855px">OUR <span class="red">SERVICES</span></h2>

<div class="svc-card" role="img" aria-label="Technician holding a tablet beside an outdoor unit" style="left:25px;background:linear-gradient(180deg,#a9a49b,#4d5866)"><div class="cap">LOREM IPSUM DOLOR<br>SIT AMET</div></div>
<div class="svc-card" style="left:320px;background:var(--red)">
  <svg class="abs" style="left:100px;top:30px" width="66" height="66" viewBox="0 0 66 66"><rect x="13" y="13" width="40" height="40" transform="rotate(45 33 33)" fill="#fff"/><circle cx="33" cy="33" r="9" fill="none" stroke="#d71e25" stroke-width="4"/><circle cx="33" cy="33" r="3" fill="#d71e25"/></svg>
  <div class="abs" style="top:137px;width:100%;text-align:center;color:#fff;font-weight:700;font-size:16px;line-height:26px">LOREM IPSUM DOLOR<br>SIT AMET</div>
  <div class="abs" style="top:193px;left:22px;width:223px;text-align:center;color:#fff;font-size:15px;line-height:26px">Lorem ipsum dolor sit amet, con sectetur adipiscing elit, sed do eiusmod tempor incididunt ut labore sed dolorea.</div>
  <div class="abs" style="top:312px;width:100%;text-align:center;color:#fff;font-weight:700;font-size:14px;text-decoration:underline">LEARN MORE</div>
</div>
<div class="svc-card" role="img" aria-label="Smiling technician servicing an outdoor condenser" style="left:614px;background:linear-gradient(180deg,#9aa0a8,#3d4a5b)"><div class="cap">LOREM IPSUM DOLOR<br>SIT AMET</div></div>
<div class="svc-card" role="img" aria-label="Technician installing an indoor split unit for a customer" style="left:908px;background:linear-gradient(180deg,#d8dde4,#6a7c93)"><div class="cap">LOREM IPSUM DOLOR<br>SIT AMET</div></div>

<!-- products -->
<div class="abs" style="left:0;top:2405px;width:1200px;height:595px;background:linear-gradient(180deg,var(--navy),var(--navy-dark))"></div>
<h2 class="abs display section-title" style="top:2488px;color:#fff">SHOP OUR PRODUCTS</h2>
<div class="prod-card" style="left:112px"><div class="ph" role="img" aria-label="AC compressor" style="left:82px;top:35px;width:140px;height:140px;border-radius:50%;background:radial-gradient(#d9dce0,#8c939b)"></div><div class="name">LOREM IPSUM DOLOR<br>SIT AMET</div><div class="go"></div></div>
<div class="prod-card" style="left:448px"><div class="ph" role="img" aria-label="Condenser fan motor" style="left:82px;top:35px;width:140px;height:140px;border-radius:50%;background:radial-gradient(#777,#1d1d1d)"></div><div class="name">LOREM IPSUM DOLOR<br>SIT AMET</div><div class="go"></div></div>
<div class="prod-card" style="left:785px"><div class="ph" role="img" aria-label="Blower motor assembly" style="left:82px;top:35px;width:140px;height:140px;border-radius:50%;background:radial-gradient(#666,#222)"></div><div class="name">LOREM IPSUM DOLOR<br>SIT AMET</div><div class="go"></div></div>
<svg class="abs" style="left:242px;top:2864px" width="120" height="20"><path d="M18 3l5 6-5 6" fill="none" stroke="#fff" stroke-width="2"/></svg>
<svg class="abs" style="left:578px;top:2864px" width="120" height="20"><path d="M18 3l5 6-5 6" fill="none" stroke="#fff" stroke-width="2"/></svg>
<svg class="abs" style="left:915px;top:2864px" width="120" height="20"><path d="M18 3l5 6-5 6" fill="none" stroke="#fff" stroke-width="2"/></svg>
<div class="arrow" style="left:-17px;top:2726px"></div>
<svg class="abs" style="left:4px;top:2736px" width="12" height="14"><path d="M9 1 3 7l6 6" fill="none" stroke="#d71e25" stroke-width="2"/></svg>
<div class="arrow" style="left:1183px;top:2726px"></div>
<svg class="abs" style="left:1184px;top:2736px" width="12" height="14"><path d="M3 1l6 6-6 6" fill="none" stroke="#d71e25" stroke-width="2"/></svg>

<!-- testimonials -->
<h2 class="abs display section-title navy" style="top:3110px">TESTIMONIALS</h2>
<div class="testi" style="left:112px"><div class="stars">★★★★★</div><p>Lorem ipsum dolor sit amet, consectetur adipiscing elit, sed do eiusmod tempor incididunt ut labore et dolore magna aliqu ad minim veniam, quisea.</p><hr><div class="who"><div class="avatar" role="img" aria-label="Customer portrait" style="background:#e6b89a"></div><div><b>JOHN SMITH,</b><span>TAMPA BAY</span></div></div></div>
<div class="testi" style="left:447px"><div class="stars">★★★★★</div><p>Lorem ipsum dolor sit amet, consectetur adipiscing elit, sed do eiusmod tempor incididunt ut labore et dolore magna aliqu ad minim veniam, quisea.</p><hr><div class="who"><div class="avatar" role="img" aria-label="Customer portrait" style="background:#6b4a3a"></div><div><b>LAURA,</b><span>TAMPA BAY</span></div></div></div>
<div class="testi" style="left:783px"><div class="stars">★★★★★</div><p>Lorem ipsum dolor sit amet, consectetur adipiscing elit, sed do eiusmod tempor incididunt ut labore et dolore magna aliqu ad minim veniam, quisea.</p><hr><div class="who"><div class="avatar" role="img" aria-label="Customer portrait" style="background:#c9a992"></div><div><b>JOHN SMITH,</b><span>TAMPA BAY</span></div></div></div>
<svg class="abs" style="left:560px;top:3498px" width="82" height="14"><circle cx="7" cy="7" r="5" fill="#ddd"/><circle cx="29" cy="7" r="5" fill="#d71e25"/><circle cx="51" cy="7" r="5" fill="#ddd"/><circle cx="73" cy="7" r="5" fill="#ddd"/></svg>

<!-- contact -->
<div class="abs" role="img" aria-label="Technician working on an air conditioning unit, red tinted" style="left:0;top:3595px;width:1200px;height:650px;background:linear-gradient(135deg,#e2262d,#c4161d 60%,#d71e25)"></div>
<h2 class="abs display section-title" style="top:3670px;color:#fff">CONTACT US</h2>
<div class="field" style="left:235px;top:3752px;width:360px;height:38px">Full Name</div>
<div class="field" style="left:235px;top:3804px;width:360px;height:38px">Phone</div>
<div class="field" style="left:235px;top:3855px;width:360px;height:38px">Email</div>
<div class="field" style="left:607px;top:3752px;width:359px;height:143px">Type Your Message</div>
<div class="btn" style="left:515px;top:3918px;width:168px;height:44px;background:var(--navy)">SEND MESSAGE</div>

<!-- footer -->
<svg class="abs" style="left:0;top:4010px" width="1200" height="518" viewBox="0 0 1200 518">
  <polygon points="0,225 598,0 1200,225 1200,518 0,518" fill="#fff"/>
  <polygon points="0,245 598,20 1200,245 1200,518 0,518" fill="#1f3170"/>
</svg>
<div class="abs" style="left:475px;top:4150px;width:250px;display:flex;align-items:center;justify-content:center;gap:10px;color:#fff;font-weight:700;font-size:19px;line-height:1.2;text-align:left">
  <span style="width:30px;height:30px;border-radius:50%;background:#fff;flex:none"></span><span>COASTAL BREEZE<br>COOLING COMPANY</span>
</div>

<div class="foot-h" style="left:112px">NAVIGATION</div>
<div class="foot-list" style="left:112px">Home<br>About Us<br>Our Services<br>Our Products<br>Contact Us</div>
<div class="foot-h" style="left:335px">QUICK LINKS</div>
<div class="foot-list" style="left:335px">Site Map<br>Privacy Policy<br>Terms And Conditions<br>Disclaimer</div>
<div class="foot-h" style="left:580px">CONTACT</div>
<svg class="abs" style="left:580px;top:4292px" width="18" height="24" viewBox="0 0 24 32"><path fill="#d71e25" d="M12 0a11 11 0 0 0-11 11c0 8 11 21 11 21s11-13 11-21A11 11 0 0 0 12 0zm0 15a4 4 0 1 1 0-8 4 4 0 0 1 0 8z"/></svg>
<div class="foot-list" style="left:620px;top:4290px;line-height:25px">465, Lorum Ipsum Dolore Sed,<br>Tampa Bay</div>
<svg class="abs" style="left:580px;top:4354px" width="20" height="20" viewBox="0 0 24 24"><path fill="#d71e25" d="M6.6 10.8a15 15 0 0 0 6.6 6.6l2.2-2.2c.3-.3.7-.4 1-.2 1.1.4 2.3.6 3.6.6.6 0 1 .4 1 1V20c0 .6-.4 1-1 1A17 17 0 0 1 3 4c0-.6.4-1 1-1h3.5c.6 0 1 .4 1 1 0 1.2.2 2.4.6 3.6.1.3 0 .7-.2 1z"/></svg>
<div class="foot-list" style="left:620px;top:4350px">+1 (888) 888 8888</div>
<svg class="abs" style="left:580px;top:4396px" width="22" height="18" viewBox="0 0 22 18"><rect x="1" y="1" width="20" height="16" fill="none" stroke="#d71e25" stroke-width="2"/><path d="M1 2l10 8 10-8" fill="none" stroke="#d71e25" stroke-width="2"/></svg>
<div class="foot-list" style="left:620px;top:4390px">info@coastalbreezecooling.com</div>
<div class="foot-h" style="left:871px">OPENING HOURS</div>
<svg class="abs" style="left:871px;top:4293px" width="22" height="22" viewBox="0 0 22 22"><circle cx="11" cy="11" r="9" fill="none" stroke="#d71e25" stroke-width="2"/><path d="M11 5v6l4 3" fill="none" stroke="#d71e25" stroke-width="2"/></svg>
<div class="foot-list" style="left:912px;top:4290px;line-height:25px">Opening :<br>Monday-friday 8am-4:30pm<br>Sat &amp; Sun | Closed</div>

<div class="abs" style="left:0;top:4470px;width:1200px;text-align:center;color:#fff;font-size:11px">© 2024 COASTAL BREEZE COOLING COMPANY &nbsp;|&nbsp; All Rights Reserved</div>
<div class="social" style="left:962px;background:var(--red)"></div>
<div class="social" style="left:1007px"></div>
<div class="social" style="left:1052px"></div>

</body>
</html>
```